Business Card Design

Just looking for a good designs that looks good with our company logo. I'd like it to be simple and to the point. Just including contact information, our logo, and my name somewhere on the card so future clients know who they're contacting, and a couple services offered. The two images I attached are pictures of our logo. I don't care which color they they are, I just attached both images to give a reference of logo colors depending on the color of the card.
Names: Carl Whitby
Phone: 816-555-0147
Email: greenstripeyard@fernmail.test
Services offered:
Mowing
Fertilization
Aeration
Bed & tree maintenance
and more.
Business
Names: Carl Whitby
Phone: 816-555-0147
(no website)

```html
<!DOCTYPE html>
<html lang="en">
<head>
<meta charset="utf-8">
<title>Greenstripe Yard Care – Business Card</title>
<link rel="stylesheet" href="https://fonts.googleapis.com/css2?family=Lato:wght@400;700;900&display=swap">
<style>
  :root {
    --backdrop: #2a2a2c;
    --card-white: #f4f4f2;
    --brand-red: #d8432f;
    --brand-red-deep: #c23a28;
    --navy: #2b2f40;
    --white: #ffffff;
  }
  * { box-sizing: border-box; margin: 0; padding: 0; }
  html, body {
    width: 1200px; height: 900px; overflow: hidden;
    background: var(--backdrop);
    font-family: "Lato", sans-serif;
  }
  .card {
    position: absolute; left: 100px; top: 160px;
    width: 1000px; height: 580px;
    display: flex;
    background: var(--brand-red);
    box-shadow: 0 18px 40px rgba(0,0,0,.45);
  }
  .card__brand {
    width: 430px; height: 100%;
    background: var(--card-white);
    display: flex; align-items: center; justify-content: center;
    gap: 16px;
  }
  .brand-dot {
    width: 34px; height: 34px; border-radius: 50%;
    background: var(--brand-red);
    flex: none;
  }
  .brand-name {
    font-weight: 900; font-size: 34px; line-height: 1.1;
    color: var(--navy); letter-spacing: 1px; text-transform: uppercase;
  }
  .card__divider {
    width: 44px; height: 100%;
    background: linear-gradient(to right,
      var(--brand-red) 0 10px, var(--card-white) 10px 22px,
      var(--brand-red) 22px 32px, var(--card-white) 32px 44px);
  }
  .card__details {
    flex: 1;
    background: linear-gradient(160deg, var(--brand-red), var(--brand-red-deep));
    padding: 70px 60px 0 80px;
  }
  .person { text-align: center; margin-bottom: 90px; }
  .person__name {
    font-weight: 900; font-size: 28px; color: var(--navy);
    letter-spacing: .5px; text-transform: uppercase;
  }
  .person__role {
    font-weight: 700; font-size: 15px; color: var(--white);
    letter-spacing: 1px; text-transform: uppercase; margin-top: 2px;
  }
  .contact { list-style: none; }
  .contact__item {
    display: flex; align-items: center; gap: 16px;
    color: var(--white); font-weight: 700; font-size: 22px;
    margin-bottom: 18px;
  }
  .contact__icon { width: 24px; height: 24px; flex: none; }
  .services { margin-top: 28px; }
  .services__label {
    display: block; width: 270px; margin-left: 90px;
    background: var(--navy); color: var(--white);
    font-size: 22px; font-weight: 400; letter-spacing: .5px;
    text-align: center; padding: 8px 0;
  }
  .services__list {
    margin-top: 22px;
    color: var(--navy); font-weight: 700; font-size: 23px; line-height: 1.3;
  }
</style>
</head>
<body>
  <article class="card">
    <section class="card__brand">
      <span class="brand-dot"></span>
      <span class="brand-name">Greenstripe<br>Yard Care</span>
    </section>
    <div class="card__divider"></div>
    <section class="card__details">
      <header class="person">
        <h1 class="person__name">Carl Whitby</h1>
        <p class="person__role">Designation</p>
      </header>
      <ul class="contact">
        <li class="contact__item">
          <svg class="contact__icon" viewBox="0 0 24 24" aria-hidden="true">
            <path fill="#fff" d="M3 8c0-2 4-4 9-4s9 2 9 4v2h-5V8H8v2H3z"/>
            <rect x="5" y="11" width="14" height="9" rx="1.5" fill="#fff"/>
            <circle cx="12" cy="15.5" r="2.4" fill="#d8432f"/>
          </svg>
          816-555-0147
        </li>
        <li class="contact__item">
          <svg class="contact__icon" viewBox="0 0 24 24" aria-hidden="true">
            <rect x="2" y="5" width="20" height="14" rx="1" fill="#fff"/>
            <path d="M2.5 5.5 12 13l9.5-7.5" fill="none" stroke="#d8432f" stroke-width="1.6"/>
          </svg>
          greenstripeyard@fernmail.test
        </li>
      </ul>
      <div class="services">
        <span class="services__label">SERVICES OFFERED</span>
        <p class="services__list">Mowing / Fertilization / Aeration<br>Bed &amp; tree Maintenance &amp; more.</p>
      </div>
    </section>
  </article>
</body>
</html>
```